Tutoring Site Hero Image Design

Updated Hero Concept for BrightHarborLessons.com

Create a hero that communicates “high quality, in-person private tutoring for all ages,” with warmth, credibility, and a real-life feel. The hero should move away from generic stock photography and better reflect the moments that make our service different: tutors meeting students where they are, one-on-one engagement, and a range of ages.

What the New Hero Should Convey
1. In-person, private, one-on-one support
This is the core differentiator, so the visual should feel intimate, focused, and real. Avoid anything that resembles online learning settings or learning-center classrooms.

2. Coverage of age ranges without clutter
We serve elementary through college. We do not need multiple students in the hero, but the chosen student should not skew strongly to one age group. Aim for a middle-ground age that feels inclusive, for example a middle schooler or early high schooler.

3. Realistic, authentic moments
Use photography that feels candid and warm. Natural light, home settings, kitchen tables, quiet study nooks, or library corners work well. Avoid staged stock looks, harsh lighting, or exaggerated classroom setups.

Design the hero at 2400 × 1200 px, with the focal point on the right side, safe area leaving room on the left for a stacked headline and form.

Images that I've shared as just thought starters and do not need to be used in the design.

Font styles to use
Sans Serif

Colors
0054AA
0677BA
7BADD7
CADEEF
E8F1F8
EB3D1F
EC4F4E
F09395
F8D3D4
FCEDEE
6B429C
8869AF
B7A5CE
E3DAEB
F3F0F8

```html
<!DOCTYPE html>
<html lang="en">
<head>
<meta charset="utf-8">
<title>BrightHarborLessons.com — Hero Concepts</title>
<link rel="stylesheet" href="https://fonts.googleapis.com/css2?family=Poppins:wght@700&family=Roboto:wght@400;700&display=swap">
<style>
  :root {
    --stage: #535353;
    --navy: #0a1585;
    --navy-deep: #020e6e;
    --red: #e4002b;
    --red-deep: #c0001e;
    --wine: #5e0a3c;
    --white: #ffffff;
    --field-blue: rgba(110, 120, 200, 0.45);
    --field-violet: rgba(130, 110, 190, 0.45);
    --photo-warm: #c9a27a;
    --photo-light: #e9e6e4;
  }
  * { box-sizing: border-box; margin: 0; padding: 0; }
  html, body {
    width: 1130px; height: 1200px; overflow: hidden;
    background: var(--stage);
  }
  .board { position: relative; width: 1130px; height: 1200px; }

  .hero {
    position: absolute; left: 43px; width: 1043px; height: 521px;
    overflow: hidden;
    box-shadow: 0 18px 30px rgba(0,0,0,0.35);
  }
  .hero--blue { top: 57px; }
  .hero--red { top: 621px; }

  .hero__photo {
    position: absolute; inset: 0 0 0 auto; width: 62%;
  }
  .hero--blue .hero__photo {
    background:
      radial-gradient(ellipse at 75% 55%, var(--photo-warm) 0%, rgba(201,162,122,0) 45%),
      linear-gradient(180deg, var(--photo-light) 0%, #d8d2cc 60%, #b9b3b0 100%);
  }
  .hero--red .hero__photo {
    background:
      radial-gradient(ellipse at 60% 60%, #c7a9a2 0%, rgba(199,169,162,0) 50%),
      linear-gradient(180deg, #ece9e8 0%, #dcd7d6 60%, #a8a9b3 100%);
  }
  .hero--blue .hero__wash {
    position: absolute; inset: 0;
    background:
      linear-gradient(90deg, var(--navy-deep) 0%, var(--navy) 38%, rgba(12,24,140,0.75) 52%, rgba(30,40,140,0.15) 68%, rgba(30,40,140,0) 80%),
      linear-gradient(0deg, rgba(2,14,110,0.5) 0%, rgba(2,14,110,0) 30%);
  }
  .hero--red .hero__wash {
    position: absolute; inset: 0;
    background:
      linear-gradient(180deg, rgba(228,0,43,0.9) 0%, rgba(160,10,70,0.6) 50%, rgba(2,14,110,0.85) 100%),
      linear-gradient(90deg, rgba(0,0,0,0) 40%, rgba(255,255,255,0) 70%);
    -webkit-mask-image: linear-gradient(90deg, #000 40%, rgba(0,0,0,0.35) 62%, transparent 80%);
    mask-image: linear-gradient(90deg, #000 40%, rgba(0,0,0,0.35) 62%, transparent 80%);
  }
  .hero__decor { position: absolute; inset: 0; }

  .hero__card {
    position: absolute; left: 86px; top: 45px; width: 319px; bottom: 0;
    border-radius: 24px 24px 0 0;
    background: linear-gradient(180deg, rgba(80,10,60,0.75) 0%, rgba(40,20,110,0.8) 60%, rgba(2,14,110,0.85) 100%);
  }

  .hero__content { position: absolute; left: 112px; top: 62px; width: 265px; }
  .headline {
    font-family: "Poppins", sans-serif; font-weight: 700;
    font-size: 32px; line-height: 35px; color: var(--white);
    letter-spacing: -0.3px;
  }
  .headline__line { display: block; white-space: nowrap; }
  .headline__mark {
    background-repeat: no-repeat;
    background-size: 100% 6px; background-position: 0 88%;
  }
  .hero--blue .headline__mark { background-image: linear-gradient(var(--red), var(--red)); }
  .hero--red .headline__mark { background-image: linear-gradient(var(--navy), var(--navy)); }

  .lead-form { position: absolute; left: 113px; top: 171px; width: 263px; }
  .lead-form__field {
    display: block; width: 263px; height: 41px; margin-bottom: 8px;
    border: 1.5px solid var(--white); border-radius: 4px;
    padding: 12px 16px;
    font-family: "Roboto", sans-serif; font-size: 8.5px; color: var(--white);
  }
  .hero--blue .lead-form__field { background: var(--field-blue); }
  .hero--red .lead-form__field { background: var(--field-violet); }
  .lead-form__field--message { height: 79px; margin-bottom: 9px; }
  .lead-form__submit {
    display: block; margin-left: 1px; width: 260px; height: 39px;
    background: var(--red); border-radius: 3px; border: none;
    font-family: "Roboto", sans-serif; font-weight: 700; font-size: 8.5px;
    color: var(--white); text-align: center; line-height: 39px;
  }
</style>
</head>
<body>
<main class="board">

  <section class="hero hero--blue">
    <div class="hero__photo" role="img" aria-label="Photo: a tutor and a student smiling while reading a tablet together at a table with a dictionary"></div>
    <div class="hero__wash"></div>
    <div class="hero__content">
      <h1 class="headline">
        <span class="headline__line"><span class="headline__mark">Local Tutors.</span></span>
        <span class="headline__line">1-on-1 Learning.</span>
        <span class="headline__line">Real Results.</span>
      </h1>
    </div>
    <form class="lead-form">
      <div class="lead-form__field">Name</div>
      <div class="lead-form__field">Email address</div>
      <div class="lead-form__field">Phone</div>
      <div class="lead-form__field lead-form__field--message">Message</div>
      <div class="lead-form__submit">SUBMIT NOW</div>
    </form>
  </section>

  <section class="hero hero--red">
    <div class="hero__photo" role="img" aria-label="Photo: a tutor sitting beside a young student working on a laptop at home"></div>
    <div class="hero__wash"></div>
    <svg class="hero__decor" width="1043" height="521" viewBox="0 0 1043 521" aria-hidden="true">
      <circle cx="210" cy="-30" r="270" fill="#e4002b" opacity="0.85"/>
      <path d="M425 128 Q540 95 577 0" fill="none" stroke="#e6e2e6" stroke-width="3"/>
    </svg>
    <div class="hero__card"></div>
    <div class="hero__content">
      <h1 class="headline">
        <span class="headline__line"><span class="headline__mark">Local Tutors.</span></span>
        <span class="headline__line">1-on-1 Learning.</span>
        <span class="headline__line">Real Results.</span>
      </h1>
    </div>
    <form class="lead-form">
      <div class="lead-form__field">Name</div>
      <div class="lead-form__field">Email address</div>
      <div class="lead-form__field">Phone</div>
      <div class="lead-form__field lead-form__field--message">Message</div>
      <div class="lead-form__submit">SUBMIT NOW</div>
    </form>
  </section>

</main>
</body>
</html>
```